Website for enterprise software start-up

We need a new Wordpress website. We are an early stage start-up focused on mobile video technology for cellular operators. The audience is strategy, marketing and customer acquisition execs from the operators.

The purpose of the site is to act as a sales brochure and capture leads. A demo app can be downloaded from the current site, want to put that behind a contact form.

Current website is at www.velmora.tv. Similar number of pages. Looking for a clean design template, with minimal customization. Blog will remain as is.

Want to be able to modify the copy via Wordpress. Reference designs I like: quandrix.com, briskfold7metrics.com

Target Market(s)

Mobile operators and MVNOs in the US and Asia Pacific regions

Industry/Entity Type

Business Software

Coding

Coded - Design and coding required

Number of Pages Required

4 page

Font styles to use
Sans Serif

Colors
f78f20

Requirements
Must have
• Form for downloading sample apps.
• Landing page with image, Product, Blog, About, Contact
• Team page

```html
<!DOCTYPE html>
<html lang="en">
<head>
<meta charset="utf-8">
<title>Velmora Media – High Quality Mobile Engagement</title>
<link rel="stylesheet" href="https://fonts.googleapis.com/css2?family=Montserrat:wght@400;600&family=Open+Sans:ital,wght@0,400;0,600;0,700;1,400&display=swap">
<style>
:root{
  --orange:#e0700f;
  --ink:#2b2b2b;
  --text:#555;
  --muted:#777;
  --light:#f1f1f1;
  --dark:#1f1814;
  --white:#fff;
  --logo-grey:#8d8d8d;
}
*{box-sizing:border-box;margin:0;padding:0}
html,body{width:1200px;height:3509px;overflow:hidden}
body{font-family:"Open Sans",Arial,sans-serif;color:var(--text);background:var(--white);position:relative}
section,footer,header{position:relative;width:1200px;overflow:hidden}
.abs{position:absolute}
.photo{position:absolute;inset:0}
h2.section-title{position:absolute;left:0;width:1200px;text-align:center;font-family:"Montserrat",Arial,sans-serif;font-weight:400;font-size:36px;line-height:44px;letter-spacing:1px;color:var(--ink);text-transform:uppercase}
.btn{position:absolute;background:var(--orange);color:var(--white);font-size:15px;display:flex;align-items:center;justify-content:center;gap:8px}

/* hero */
.hero{height:657px}
.hero .photo{background:radial-gradient(ellipse at 65% 35%,#6a5446 0%,#3a2c24 40%,#1a1411 75%)}
.brand{left:100px;top:47px;display:flex;align-items:center;gap:10px;color:var(--white)}
.brand-mark{width:50px;height:50px;background:var(--orange)}
.brand-name{font-family:"Open Sans",sans-serif;font-weight:700;font-size:42px;line-height:1}
.brand-sub{font-weight:700;font-size:11px;letter-spacing:3px;display:block;margin-top:2px}
.menu{right:100px;top:72px;width:24px}
.menu span{display:block;height:3px;background:var(--white);margin-bottom:5px}
.hero-title{left:0;width:1200px;top:300px;text-align:center;font-family:"Montserrat",sans-serif;font-weight:600;font-size:36px;line-height:44px;color:var(--white);letter-spacing:1px}
.hero-sub{left:0;width:1200px;top:350px;text-align:center;font-size:20px;color:#eee}
.hero .btn{left:522px;top:391px;width:160px;height:44px}
.scroll-down{left:574px;top:535px}

/* push notifications */
.push{height:679px}
.push .section-title{top:63px}
.lede{position:absolute;left:0;width:1200px;text-align:center;font-style:italic;font-size:14px;color:var(--text)}
.push .lede{top:125px}
.feature{position:absolute;width:260px;font-size:13px;line-height:21px;color:var(--text)}
.feature h3{font-size:13px;font-weight:700;color:var(--ink);text-transform:uppercase;margin-bottom:2px}
.feature.left{left:63px;text-align:right}
.feature.right{left:856px}
.icon-dot{position:absolute;width:62px;height:62px;border-radius:50%;background:var(--orange);display:flex;align-items:center;justify-content:center}
.device{position:absolute}

/* sample apps */
.sample{height:353px}
.sample .photo{background:linear-gradient(100deg,#2a211c 0%,#4a3c33 45%,#2c241f 100%)}
.sample .section-title{top:100px;color:var(--white)}
.store-badge{position:absolute;top:180px;width:138px;height:42px;background:#0c0c0c;border:1px solid #999;border-radius:6px}

/* native push */
.native{height:622px}
.native .section-title{top:46px}
.native .lede{left:100px;width:auto;top:140px;text-align:left}
.checklist{position:absolute;left:103px;top:200px;width:580px;list-style:none;font-size:13px;line-height:20px;color:var(--text)}
.checklist li{position:relative;padding-left:34px;margin-bottom:19px}
.checklist svg{position:absolute;left:0;top:4px}
.native .btn{left:100px;top:430px;width:160px;height:43px;font-size:14px}

/* team */
.team{height:505px;background:var(--light)}
.team .section-title{top:53px}
.member{position:absolute;top:130px;width:240px;text-align:center}
.avatar{width:146px;height:146px;margin:0 auto;border-radius:50%;border:6px solid var(--white);background:linear-gradient(#b9b3ad,#6f6760);box-shadow:0 2px 6px rgba(0,0,0,.2)}
.member h3{margin-top:32px;font-family:"Montserrat",sans-serif;font-weight:400;font-size:20px;line-height:26px;color:var(--ink);text-transform:uppercase}
.member p{margin-top:6px;font-size:13px;line-height:21px;color:var(--text)}
.socials{display:flex;justify-content:center;gap:14px;margin-top:16px}
.socials span{width:34px;height:34px;border-radius:50%;background:var(--white);border:1px solid #ddd}

/* partners */
.partners{height:218px}
.partner{position:absolute;top:89px;height:40px;display:flex;align-items:center;justify-content:center;gap:8px;font-family:"Open Sans",sans-serif;font-weight:700;color:var(--logo-grey);white-space:nowrap;overflow:hidden}
.partner .mark{flex:none;width:36px;height:36px;background:#bbb}
.partner .mark.round{border-radius:50%}
.carousel-arrow{position:absolute;top:99px}

/* contact */
.contact{height:423px}
.contact .photo{background:linear-gradient(100deg,#2b221d 0%,#3f332c 50%,#5a4d44 100%)}
.contact .section-title{top:54px;color:var(--white)}
.field{position:absolute;height:34px;border:1px solid #ccc;color:var(--white);font-size:13px;padding:8px 12px;background:transparent}
.contact .btn{left:159px;top:334px;width:126px;height:37px;font-size:13px}
.address{position:absolute;left:753px;top:125px;color:var(--white);font-size:14px;line-height:22px}
.address h4{font-weight:400;font-size:17px;margin-bottom:4px}
.address .row{display:flex;gap:12px;align-items:flex-start;margin-bottom:16px}
.address svg{flex:none;margin-top:3px}

/* footer */
.site-footer{height:52px;background:var(--orange);color:var(--white);font-size:12px}
.site-footer .copy{left:100px;top:18px}
.site-footer .follow{left:798px;top:18px}
.site-footer .dots{left:994px;top:11px;display:flex;gap:6px}
.site-footer .dots span{width:30px;height:30px;border-radius:50%;background:#3f7fd0}
</style>
</head>
<body>

<header class="hero">
  <div class="photo" role="img" aria-label="Photo of a person holding a smartphone playing video"></div>
  <div class="abs brand"><span class="brand-mark"></span><div><span class="brand-name">velmora</span><span class="brand-sub">MEDIA</span></div></div>
  <div class="abs menu"><span></span><span></span><span></span></div>
  <h1 class="abs hero-title">HIGH QUALITY MOBILE ENGAGEMENT</h1>
  <p class="abs hero-sub">We engage mobile audiences with the right video content at the perfect moment.</p>
  <a class="btn"><svg width="14" height="14" viewBox="0 0 14 14"><path d="M7 1v8M3.5 5.5 7 9l3.5-3.5M1 12h12" stroke="#fff" stroke-width="2" fill="none"/></svg>Sample apps</a>
  <svg class="abs scroll-down" width="54" height="54" viewBox="0 0 54 54"><circle cx="27" cy="27" r="25" stroke="#fff" stroke-width="2" fill="none"/><path d="M17 23l10 10 10-10" stroke="#fff" stroke-width="2.5" fill="none"/></svg>
</header>

<section class="push">
  <h2 class="section-title">Push Video Notifications</h2>
  <p class="lede">Personalised flawless HD videos, revealed at the perfect moment, as rich media notifications.</p>

  <div class="feature left" style="top:210px"><h3>Reach your mobile audience</h3>Reach your mobile audience with beautiful HD thumbnails and in-notification videos.</div>
  <div class="icon-dot" style="left:348px;top:200px"><svg width="26" height="30" viewBox="0 0 26 30"><rect x="6" y="2" width="14" height="26" rx="2" stroke="#fff" stroke-width="2.4" fill="none"/><circle cx="13" cy="23" r="1.6" fill="#fff"/></svg></div>

  <div class="feature left" style="top:357px"><h3>Guaranteed flawless</h3>Reach your mobile audience with beautiful HD thumbnails and in-notification videos.</div>
  <div class="icon-dot" style="left:348px;top:348px"><svg width="28" height="28" viewBox="0 0 28 28"><path d="M5 14l6 6 12-13" stroke="#fff" stroke-width="3.2" fill="none"/></svg></div>

  <div class="feature left" style="top:512px"><h3>Beautiful HD</h3>Monetize with beautiful HD preroll or interstitial ads. Monetize with beautiful HD preroll</div>
  <div class="icon-dot" style="left:348px;top:506px"><svg width="30" height="20" viewBox="0 0 30 20"><rect x="1" y="3" width="19" height="14" rx="2" fill="#fff"/><path d="M21 10l8-6v12z" fill="#fff"/></svg></div>

  <svg class="device" style="left:487px;top:176px" width="210" height="449" viewBox="0 0 210 449">
    <defs><linearGradient id="scr1" x1="0" y1="0" x2="0" y2="1"><stop offset="0" stop-color="#5d7c45"/><stop offset=".55" stop-color="#7b6aa8"/><stop offset="1" stop-color="#3a3a5a"/></linearGradient></defs>
    <rect x="2" y="2" width="206" height="445" rx="30" fill="#f4f4f4" stroke="#cfcfcf" stroke-width="3"/>
    <rect x="78" y="28" width="54" height="6" rx="3" fill="#c8c8c8"/>
    <circle cx="105" cy="408" r="20" fill="none" stroke="#c8c8c8" stroke-width="3"/>
    <rect x="14" y="62" width="182" height="318" fill="url(#scr1)" role="img" aria-label="Phone lock screen showing a video notification"/>
  </svg>

  <div class="icon-dot" style="left:774px;top:200px"><svg width="26" height="28" viewBox="0 0 26 28"><rect x="3" y="2" width="14" height="24" rx="2" stroke="#fff" stroke-width="2.4" fill="none"/><circle cx="19" cy="17" r="5" fill="#fff"/></svg></div>
  <div class="feature right" style="top:210px"><h3>Existing apps</h3>Easily added to your existing apps within one hour. Easily added to your existing apps</div>

  <div class="icon-dot" style="left:774px;top:348px"><svg width="32" height="20" viewBox="0 0 32 20"><path d="M2 10Q16-6 30 10Q16 26 2 10z" fill="#fff"/><circle cx="16" cy="10" r="5" fill="#e0700f"/></svg></div>
  <div class="feature right" style="top:357px"><h3>Viewer interests</h3>Content is personalised based on viewer interests and mobile viewing habits.</div>

  <div class="icon-dot" style="left:774px;top:506px"><svg width="24" height="24" viewBox="0 0 24 24"><path d="M12 2v13M6 9l6 6 6-6M2 21h20" stroke="#fff" stroke-width="2.6" fill="none"/></svg></div>
  <div class="feature right" style="top:512px"><h3>Easy downloaded</h3>Personalised flawless HD videos, revealed at the perfect moment, as rich media notifications.</div>
</section>

<section class="sample">
  <div class="photo" role="img" aria-label="Photo of a hand holding a phone at a café table"></div>
  <h2 class="section-title">Sample Apps</h2>
  <span class="store-badge" style="left:459px"></span>
  <span class="store-badge" style="left:604px"></span>
</section>

<section class="native">
  <h2 class="section-title">Native Push Video</h2>
  <p class="lede">Personalised flawless HD videos, discoverable in-app, and playable even when offline.</p>
  <ul class="checklist">
    <li><svg width="14" height="12" viewBox="0 0 14 12"><path d="M1 6l4 4 8-9" stroke="#e0700f" stroke-width="2.4" fill="none"/></svg>Guarantee your audience never gets frustrated with a poor quality mobile video streaming experience.</li>
    <li><svg width="14" height="12" viewBox="0 0 14 12"><path d="M1 6l4 4 8-9" stroke="#e0700f" stroke-width="2.4" fill="none"/></svg>Instant video playback, zero buffering, HD quality guaranteed - even when offline.</li>
    <li><svg width="14" height="12" viewBox="0 0 14 12"><path d="M1 6l4 4 8-9" stroke="#e0700f" stroke-width="2.4" fill="none"/></svg>Content is personalised based on viewer interests and mobile viewing habits.</li>
    <li><svg width="14" height="12" viewBox="0 0 14 12"><path d="M1 6l4 4 8-9" stroke="#e0700f" stroke-width="2.4" fill="none"/></svg>Monetize with beautiful HD preroll or interstitial ads.</li>
    <li><svg width="14" height="12" viewBox="0 0 14 12"><path d="M1 6l4 4 8-9" stroke="#e0700f" stroke-width="2.4" fill="none"/></svg>Use your existing content management and hosting systems.</li>
  </ul>
  <a class="btn">View more info</a>

  <svg class="device" style="left:779px;top:160px" width="300" height="420" viewBox="0 0 300 400">
    <rect x="2" y="24" width="150" height="350" rx="24" fill="#f4f4f4" stroke="#cfcfcf" stroke-width="3"/>
    <rect x="12" y="70" width="120" height="250" fill="#1f5f95" role="img" aria-label="Phone screen showing an app interface"/>
    <rect x="94" y="2" width="196" height="390" rx="28" fill="#1f9ad6"/>
    <rect x="104" y="14" width="176" height="366" rx="22" fill="#111"/>
    <rect x="112" y="62" width="160" height="278" fill="#3a3631" role="img" aria-label="Phone screen listing movie trailers"/>
    <circle cx="192" cy="360" r="13" fill="none" stroke="#444" stroke-width="2"/>
  </svg>
</section>

<section class="team">
  <h2 class="section-title">Our Team</h2>
  <div class="member" style="left:126px"><div class="avatar" role="img" aria-label="Portrait of Ravi, CTO"></div><h3>Ravi_CTO</h3><p>Personalised flawless HD videos, revealed at the perfect moment, as rich media</p><div class="socials"><span></span><span></span><span></span></div></div>
  <div class="member" style="left:369px"><div class="avatar" role="img" aria-label="Portrait of Marcus"></div><h3>Marcus</h3><p>Personalised flawless HD videos, revealed at the perfect moment, as rich media</p><div class="socials"><span></span><span></span><span></span></div></div>
  <div class="member" style="left:617px"><div class="avatar" role="img" aria-label="Portrait of Glen"></div><h3>Glen</h3><p>Personalised flawless HD videos, revealed at the perfect moment, as rich media</p><div class="socials"><span></span><span></span><span></span></div></div>
  <div class="member" style="left:858px"><div class="avatar" role="img" aria-label="Portrait of Tobias"></div><h3>Tobias</h3><p>Personalised flawless HD videos, revealed at the perfect moment, as rich media</p><div class="socials"><span></span><span></span><span></span></div></div>
</section>

<section class="partners">
  <svg class="carousel-arrow" style="left:92px" width="16" height="20" viewBox="0 0 16 20"><path d="M12 3 5 10l7 7" stroke="#888" stroke-width="3" fill="none"/></svg>
  <div class="partner" style="left:128px;width:212px;font-size:28px"><span class="mark round"></span>Streamlet</div>
  <div class="partner" style="left:366px;width:122px;font-size:16px">Harbor Hoops</div>
  <div class="partner" style="left:506px;width:190px;font-size:15px"><span class="mark"></span>Cadence Records</div>
  <div class="partner" style="left:716px;width:112px;font-size:15px">Ice Pioneers</div>
  <div class="partner" style="left:852px;width:176px;font-size:28px">Brightwave</div>
  <svg class="carousel-arrow" style="left:1094px" width="16" height="20" viewBox="0 0 16 20"><path d="M4 3l7 7-7 7" stroke="#888" stroke-width="3" fill="none"/></svg>
</section>

<section class="contact">
  <div class="photo" role="img" aria-label="Photo of a person using a phone beside a laptop"></div>
  <h2 class="section-title">Contact Us</h2>
  <div class="field" style="left:159px;top:138px;width:275px">Name</div>
  <div class="field" style="left:442px;top:138px;width:275px">Mail</div>
  <div class="field" style="left:159px;top:182px;width:275px">Phone</div>
  <div class="field" style="left:442px;top:182px;width:275px">Subject</div>
  <div class="field" style="left:159px;top:226px;width:558px;height:94px">Message</div>
  <a class="btn">Submit</a>
  <div class="address">
    <h4>Address</h4>
    <div class="row"><svg width="14" height="18" viewBox="0 0 14 18"><path d="M7 1a6 6 0 0 0-6 6c0 5 6 10 6 10s6-5 6-10a6 6 0 0 0-6-6z" fill="#fff"/><circle cx="7" cy="7" r="2.2" fill="#3f332c"/></svg><span>2207 Larkspur Ave<br>Fernwood, MI 48012</span></div>
    <div class="row"><svg width="16" height="12" viewBox="0 0 16 12"><rect width="16" height="12" rx="1" fill="#fff"/><path d="M1 1l7 6 7-6" stroke="#3f332c" stroke-width="1.5" fill="none"/></svg><span>info@velmora.tv</span></div>
    <div class="row"><svg width="16" height="16" viewBox="0 0 16 16"><path d="M3 1l3 3-2 2a9 9 0 0 0 6 6l2-2 3 3-2 2C7 15 1 9 1 3z" fill="#fff"/></svg><span>555-014-2271</span></div>
    <div class="row"><svg width="16" height="16" viewBox="0 0 16 16"><rect x="1" y="5" width="14" height="9" rx="1" fill="#fff"/><rect x="4" y="1" width="8" height="5" fill="#fff"/></svg><span>555-014-2284</span></div>
  </div>
</section>

<footer class="site-footer">
  <span class="abs copy">© velmora 2016. All Rights Reserved</span>
  <span class="abs follow">Connect with our social network :</span>
  <div class="abs dots"><span></span><span></span><span></span></div>
</footer>

</body>
</html>
```